Custom Seed Packet design for Flower Farm

We need a design for our seeds packets.
The design will be a kind of "fill in the blanks" as we need the design to be adaptable for multiple varieties of seed. We will be using the design for a rubber stamp.
Our seed packets are 90x90mm in size.
Black logo only. No colour required.
A vintage botanical influence is desired.
Will need to include the following info,
"Wrenfield Gable Co logo" , "Seeds", "Plant Type", "Variety", "Harvested"

```html
<!DOCTYPE html>
<html lang="en">
<head>
<meta charset="utf-8">
<title>Wrenfield Gable Co. Flower Farm — Seed Packet</title>
<link href="https://fonts.googleapis.com/css2?family=IM+Fell+English&family=Lato:wght@400&display=swap" rel="stylesheet">
<style>
  :root {
    --kraft: #d6c29c;
    --kraft-light: #e2d3b4;
    --kraft-shade: #c7b089;
    --ink: #231d17;
    --ink-soft: #4a3f33;
    --ornament-dark: #3a3128;
    --ornament-mid: #a8977a;
  }
  * { margin: 0; padding: 0; box-sizing: border-box; }
  html, body { width: 1122px; height: 1200px; overflow: hidden; }
  body { background: var(--kraft); }
  .packet {
    position: relative;
    width: 1122px;
    height: 1200px;
    background: radial-gradient(ellipse at 50% 45%, var(--kraft-light) 0%, var(--kraft) 55%, var(--kraft-shade) 100%);
  }
  .corner-ornament { position: absolute; width: 184px; height: 162px; }
  .corner-ornament--tl { left: 82px; top: 196px; }
  .corner-ornament--tr { left: 838px; top: 196px; }
  .corner-ornament--bl { left: 82px; top: 886px; }
  .corner-ornament--br { left: 838px; top: 886px; }
  .title {
    position: absolute;
    top: 200px; left: 0; width: 100%;
    text-align: center;
    font-family: "IM Fell English", serif;
    font-size: 104px;
    line-height: 1;
    color: var(--ink);
  }
  .title-rule {
    position: absolute;
    left: 310px; top: 306px; width: 486px; height: 16px;
  }
  .wreath { position: absolute; left: 306px; top: 336px; width: 490px; height: 490px; }
  .brand {
    position: absolute;
    left: 361px; top: 520px; width: 380px;
    text-align: center;
    font-family: "IM Fell English", serif;
    color: var(--ink);
    font-size: 34px;
    line-height: 1.15;
  }
  .fields {
    position: absolute;
    left: 176px; top: 828px; width: 746px;
    list-style: none;
    font-family: "Lato", sans-serif;
    font-size: 22px;
    color: var(--ink-soft);
  }
  .field { display: flex; align-items: flex-end; height: 34px; }
  .field-label { white-space: nowrap; padding-right: 8px; }
  .field-line { flex: 1; border-bottom: 1.5px solid var(--ink-soft); margin-bottom: 5px; }
</style>
</head>
<body>
<main class="packet">
  <svg class="corner-ornament corner-ornament--tl" viewBox="0 0 184 162" role="img" aria-label="Vintage filigree corner ornament">
    <path d="M0 0H184V34H34V162H0Z" fill="var(--ornament-dark)" opacity="0.75"/>
  </svg>
  <svg class="corner-ornament corner-ornament--tr" viewBox="0 0 184 162" role="img" aria-label="Vintage filigree corner ornament">
    <path d="M0 0H184V162H150V34H0Z" fill="var(--ornament-dark)" opacity="0.75"/>
  </svg>
  <svg class="corner-ornament corner-ornament--bl" viewBox="0 0 184 162" role="img" aria-label="Vintage filigree corner ornament">
    <path d="M0 0H34V128H184V162H0Z" fill="var(--ornament-dark)" opacity="0.75"/>
  </svg>
  <svg class="corner-ornament corner-ornament--br" viewBox="0 0 184 162" role="img" aria-label="Vintage filigree corner ornament">
    <path d="M150 0H184V162H0V128H150Z" fill="var(--ornament-dark)" opacity="0.75"/>
  </svg>

  <h1 class="title">Seeds</h1>
  <svg class="title-rule" viewBox="0 0 486 16">
    <line x1="0" y1="8" x2="486" y2="8" stroke="var(--ink)" stroke-width="2"/>
    <circle cx="243" cy="8" r="4" fill="var(--ink)"/>
  </svg>

  <svg class="wreath" viewBox="0 0 490 490" role="img" aria-label="Circular wreath of stylised flowers framing the logo">
    <defs>
      <radialGradient id="wreathTone" cx="50%" cy="50%" r="50%">
        <stop offset="78%" stop-color="var(--ornament-mid)"/>
        <stop offset="100%" stop-color="var(--ornament-dark)"/>
      </radialGradient>
    </defs>
    <path fill-rule="evenodd" fill="url(#wreathTone)" d="M245 0a245 245 0 1 0 0.01 0ZM245 70a175 175 0 1 1 -0.01 0Z"/>
    <circle cx="245" cy="245" r="175" fill="var(--kraft-light)"/>
  </svg>

  <div class="brand">Wrenfield Gable Co.<br>Flower Farm</div>

  <ul class="fields">
    <li class="field"><span class="field-label">Seeds</span><span class="field-line"></span></li>
    <li class="field"><span class="field-label">Plant Type</span><span class="field-line"></span></li>
    <li class="field"><span class="field-label">Variety</span><span class="field-line"></span></li>
    <li class="field"><span class="field-label">Harvested</span><span class="field-line"></span></li>
  </ul>
</main>
</body>
</html>
```